Business Cards + Flyer + Letterhead for Care Recruitment Agency

We are a recruitment agency for the health & care sector. We need designs made for business cards, A5 double-sided flyer, and a letterhead template.

Our branding message is professionalism, care, compassion, expertise. We are experts in recruitment for the care & health industry.

Our logo source files and colours are here - https://www.filevault-example.net/sh/q8rn27lpzw4xkc/BBRtLm3QPW92dKfYhNvZceLmo?dl=0

For the business card, I have attached an example we like. We want a vertical business card design, something very similar to the example given. The design should match our logo in terms of brand colors. On one side should be our logo, our website (www.holbrookelune.co.uk) and Care Recruitment Specialists written somewhere visible that fits, between our logo and the website at the bottom. On the other side should be our details.

Details on the front:

Logo with slogan
Care Recruitment Specialists
www.holbrookelune.co.uk

Details on the back:

Dominic Argyros
Managing Director

Radley Court, 40-48 Pellow St, Birmingham, B7 9QX
07612 495137
dominic@holbrookelune.co.uk
www.holbrookelune.co.uk

Nadia Holbrooke
Business Development Director

07731 284956
nadia@holbrookelune.co.uk
www.holbrookelune.co.uk

For the A5 flyer, I have attached some pictures we've used for the website, which could be used for the flyer as well. To get a better idea of our branding, please visit our website - https://holbrookelune.co.uk/

The text for the flyer is also attached.

Finally, the letterhead template should be a docx template with our logo and our identifiable branding (the same shapes and matching colours you will come up with for the business cards and flyer).

```html
<!DOCTYPE html>
<html lang="en">
<head>
<meta charset="utf-8">
<title>Holbrooke Lune – Business Cards</title>
<link rel="stylesheet" href="https://fonts.googleapis.com/css2?family=Lato:wght@400;700;900&display=swap">
<style>
  :root {
    --stage: #5e5e5e;
    --navy: #1f2b63;
    --navy-deep: #18224f;
    --sky: #2f8be0;
    --sky-light: #49b3ee;
    --white: #ffffff;
    --rule: rgba(255,255,255,0.45);
  }
  * { box-sizing: border-box; margin: 0; padding: 0; }
  html, body { width: 1200px; height: 900px; overflow: hidden; }
  body {
    background: var(--stage);
    font-family: "Lato", Arial, sans-serif;
    position: relative;
  }
  .card {
    position: absolute;
    border-radius: 18px;
    overflow: hidden;
    box-shadow: 0 14px 30px rgba(0,0,0,0.35);
  }

  /* Details side (vertical) */
  .card--details {
    left: 150px; top: 200px;
    width: 330px; height: 510px;
  }
  .card__backdrop { position: absolute; inset: 0; width: 100%; height: 100%; }
  .brand {
    position: absolute;
    display: flex; align-items: center; gap: 10px;
    white-space: nowrap;
  }
  .brand__dot {
    width: 22px; height: 22px; border-radius: 50%;
    background: var(--sky);
    flex: none;
  }
  .brand__name {
    font-weight: 900; letter-spacing: 2px; text-transform: uppercase;
  }
  .brand__slogan {
    position: absolute;
    font-size: 11px; letter-spacing: 3px; text-transform: uppercase;
    white-space: nowrap;
  }
  .card--details .brand { left: 34px; top: 84px; }
  .card--details .brand__name { color: var(--navy); font-size: 20px; }
  .card--details .brand__dot { width: 20px; height: 20px; }
  .card--details .brand__slogan { left: 64px; top: 114px; color: var(--sky); font-size: 10px; }

  .details {
    position: absolute; left: 0; right: 0; top: 258px;
    text-align: center; color: var(--white);
  }
  .details__name { font-size: 24px; font-weight: 900; text-transform: uppercase; letter-spacing: 0.5px; }
  .details__role { font-size: 15px; margin-top: 3px; }
  .details__rule { width: 200px; height: 1px; background: var(--rule); margin: 10px auto; }
  .details__icons { display: flex; justify-content: center; gap: 5px; margin-bottom: 8px; }
  .details__icons svg { width: 18px; height: 18px; }
  .details__line { font-size: 15px; line-height: 1.4; }

  /* Logo side (horizontal) */
  .card--brand {
    left: 520px; top: 150px;
    width: 530px; height: 330px;
    background: var(--navy);
  }
  .card--brand .brand { left: 140px; top: 112px; }
  .card--brand .brand__name { color: var(--white); font-size: 30px; }
  .card--brand .brand__dot { width: 26px; height: 26px; background: var(--sky-light); }
  .card--brand .brand__slogan { left: 176px; top: 154px; color: var(--white); font-size: 12px; }
  .card--brand .tagline {
    position: absolute; left: 176px; top: 196px;
    color: var(--white); font-size: 17px;
  }
  .card--brand .web {
    position: absolute; left: 176px; top: 222px;
    color: var(--white); font-size: 17px;
  }
</style>
</head>
<body>

<section class="card card--details">
  <svg class="card__backdrop" viewBox="0 0 330 510" preserveAspectRatio="none" aria-hidden="true">
    <rect width="330" height="510" fill="#ffffff"/>
    <path d="M0,232 C130,232 270,180 330,40 L330,510 L0,510 Z" fill="#2f8be0"/>
    <path d="M0,240 C135,240 276,186 330,58 L330,510 L0,510 Z" fill="#1f2b63"/>
  </svg>

  <div class="brand">
    <span class="brand__dot"></span>
    <span class="brand__name">Holbrooke Lune</span>
  </div>
  <p class="brand__slogan">Care with heart</p>

  <div class="details">
    <p class="details__name">Dominic Argyros</p>
    <p class="details__role">Managing Director</p>
    <div class="details__rule"></div>
    <div class="details__icons">
      <svg viewBox="0 0 20 20" aria-label="Phone"><circle cx="10" cy="10" r="9" fill="#fff"/><path d="M7 5.5l1.8 2-1 1.2a6 6 0 0 0 3.5 3.5l1.2-1 2 1.8-1.2 1.5c-3.5 0-7.7-4.2-7.7-7.7z" fill="#1f2b63"/></svg>
      <svg viewBox="0 0 20 20" aria-label="Email"><circle cx="10" cy="10" r="9" fill="#fff"/><rect x="5" y="6.5" width="10" height="7" rx="1" fill="#1f2b63"/><path d="M5.5 7l4.5 3.6L14.5 7" stroke="#fff" stroke-width="1" fill="none"/></svg>
      <svg viewBox="0 0 20 20" aria-label="Website"><circle cx="10" cy="10" r="9" fill="#fff"/><circle cx="10" cy="10" r="5" fill="none" stroke="#1f2b63" stroke-width="1.2"/><ellipse cx="10" cy="10" rx="2.2" ry="5" fill="none" stroke="#1f2b63" stroke-width="1"/><path d="M5 10h10" stroke="#1f2b63" stroke-width="1"/></svg>
    </div>
    <p class="details__line">07612 495137</p>
    <p class="details__line">dominic@holbrookelune.co.uk</p>
    <p class="details__line">www.holbrookelune.co.uk</p>
    <div class="details__rule"></div>
    <p class="details__line">Radley Court, 40-48 Pellow St,</p>
    <p class="details__line">Birmingham, B7 9QX</p>
  </div>
</section>

<section class="card card--brand">
  <div class="brand">
    <span class="brand__dot"></span>
    <span class="brand__name">Holbrooke Lune</span>
  </div>
  <p class="brand__slogan">Care with heart</p>
  <p class="tagline">Care Recruitment Specialists</p>
  <p class="web">www.holbrookelune.co.uk</p>
</section>

</body>
</html>
```